Upmarket Dessert Lounge needs a Business Card Design

We are an upmarket dessert lounge needing a business card to match our image.

We want something that is simple yet beautiful, feminine, classy, sophisticated and elegant. We want it to stand out and don't mind if it is bold.

The design should include our logo and colours of red or maroon with gold highlights. We don't mind if black is used.

Marlow & Quince

Target Market(s)

For those who like to indulge or treat themselves and give in to their temptations on good quality desserts.

Industry/Entity Type

Business

Requirements
Must have
• Must include our logo and our name

Marlow & Quince

M & Q

```html
<!DOCTYPE html>
<html lang="en">
<head>
<meta charset="utf-8">
<title>Marlow &amp; Quince – Business Card</title>
<link href="https://fonts.googleapis.com/css2?family=Open+Sans:wght@400;600;700&display=swap" rel="stylesheet">
<style>
  :root {
    --card-black: #000000;
    --maroon: #7a1416;
    --cream: #fdd39a;
    --white: #ffffff;
    --backdrop: #d9d9db;
    --card-font: "Open Sans", Arial, sans-serif;
  }
  * { margin: 0; padding: 0; box-sizing: border-box; }
  html, body {
    width: 956px;
    height: 1200px;
    overflow: hidden;
    background: var(--backdrop);
    font-family: var(--card-font);
  }
  .card {
    position: absolute;
    width: 798px;
    height: 454px;
    border-radius: 24px;
    background: var(--card-black);
    overflow: hidden;
  }
  .card--front { left: 79px; top: 104px; }
  .card--back { left: 74px; top: 632px; height: 456px; }

  .card__shapes {
    position: absolute;
    inset: 0;
    width: 100%;
    height: 100%;
  }
  .shape--maroon { fill: var(--maroon); }
  .shape--cream { fill: var(--cream); }

  .brand-name {
    position: absolute;
    left: 0;
    width: 480px;
    top: 90px;
    text-align: center;
    color: var(--cream);
    font-size: 30px;
    font-weight: 600;
    letter-spacing: 1px;
  }

  .person {
    position: absolute;
    left: 89px;
    top: 226px;
    color: var(--cream);
    font-size: 22px;
    line-height: 30px;
  }
  .person__name { font-weight: 700; }
  .person__role { font-weight: 400; }

  .contact {
    position: absolute;
    left: 89px;
    top: 270px;
    color: var(--white);
    font-size: 18px;
    line-height: 30px;
  }
  .contact b { font-weight: 700; }
  .contact .divider { padding: 0 6px; }

  .company-info {
    position: absolute;
    left: 0;
    right: 0;
    top: 392px;
    text-align: center;
    color: var(--white);
    font-size: 18px;
    line-height: 27px;
    padding-left: 4px;
  }
  .company-info b { font-weight: 700; }
  .company-info .divider { padding: 0 4px; }

  .monogram {
    position: absolute;
    inset: 0;
    display: flex;
    align-items: center;
    justify-content: center;
    color: var(--cream);
    font-size: 110px;
    font-weight: 400;
    letter-spacing: 2px;
  }
</style>
</head>
<body>

  <section class="card card--front" aria-label="Business card front">
    <svg class="card__shapes" viewBox="0 0 798 454" preserveAspectRatio="none" aria-hidden="true">
      <path class="shape--maroon" d="M0,398 C120,365 300,372 470,362 C620,345 740,250 798,152 L798,454 L0,454 Z"/>
      <path class="shape--cream" d="M681,0 L798,0 L798,128 C740,230 620,320 476,358 C610,300 690,160 681,0 Z"/>
    </svg>

    <div class="brand-name">MARLOW &amp; QUINCE</div>

    <p class="person"><span class="person__name">Your Name -</span> <span class="person__role">Designation</span></p>

    <p class="contact">
      <b>p</b> : 123-456-7890<span class="divider">|</span><b>c</b> : 123-456-7890<br>
      <b>e</b> : name@yourwebsite.com
    </p>

    <p class="company-info">
      <b>f</b> : 123-456-7890<span class="divider">|</span><b>w</b> : www.marlowquince.com<br>
      0000, Street Name, City Name, Country Code.
    </p>
  </section>

  <section class="card card--back" aria-label="Business card back">
    <div class="monogram">M &amp; Q</div>
  </section>

</body>
</html>
```